Timber Crest Construction Needs business card

Hey we are in need of business card designs. I have upload our logo as a guideline, but free feel to run with it or come up with something unique.
Pls have fun with it and be creative. the name says it all!
i will give some directions after i see a few entries..
Updates
Logo source file has been uploaded..
Hey because of the logo is so colourful already.
Can we have a few submissions with less colour.
Also we are looking for clever/hidden/descriptive business card.

```html
<!DOCTYPE html>
<html lang="en">
<head>
<meta charset="UTF-8">
<title>Timber Crest Construction – Business Card</title>
<link href="https://fonts.googleapis.com/css2?family=Open+Sans:wght@400;600;700&display=swap" rel="stylesheet">
<style>
  :root {
    --backdrop: #e7e4df;
    --card: #ffffff;
    --ink: #1f1f1f;
    --brand-grey: #5a5f61;
    --accent-blue: #2f6fb0;
    --rule-blue: #6aa7dc;
    --mark-blue: #74b8e6;
    --shadow: rgba(0, 0, 0, 0.18);
  }
  * { margin: 0; padding: 0; box-sizing: border-box; }
  html, body {
    width: 1200px;
    height: 470px;
    overflow: hidden;
    background: var(--backdrop);
    font-family: "Open Sans", Arial, sans-serif;
  }
  .stage {
    position: relative;
    width: 1200px;
    height: 470px;
  }
  .card {
    position: absolute;
    top: 80px;
    width: 540px;
    height: 310px;
    background: var(--card);
    box-shadow: 0 6px 18px var(--shadow);
  }
  .card--front { left: 40px; }
  .card--back { left: 620px; }

  /* Wordmark */
  .wordmark {
    position: absolute;
    left: 0;
    right: 0;
    display: flex;
    align-items: center;
    justify-content: center;
    gap: 12px;
    color: var(--brand-grey);
    font-weight: 700;
    text-transform: uppercase;
  }
  .wordmark__square {
    background: var(--mark-blue);
    flex: none;
  }
  .wordmark__text {
    display: flex;
    flex-direction: column;
    line-height: 1.05;
  }
  .wordmark__sub { text-align: right; }

  .card--front .wordmark { top: 52px; }
  .card--front .wordmark__square { width: 26px; height: 26px; }
  .card--front .wordmark__main { font-size: 30px; letter-spacing: 0.5px; }
  .card--front .wordmark__sub { font-size: 10px; letter-spacing: 0.5px; }

  .card--back .wordmark { top: 112px; }
  .card--back .wordmark__square { width: 44px; height: 44px; }
  .card--back .wordmark__main { font-size: 52px; letter-spacing: 1px; }
  .card--back .wordmark__sub { font-size: 17px; letter-spacing: 1px; }

  /* Contact block */
  .contact {
    position: absolute;
    top: 188px;
    left: 0;
    right: 0;
    display: flex;
    justify-content: center;
  }
  .person {
    width: 200px;
    padding-right: 16px;
    text-align: right;
    border-right: 1.5px solid var(--rule-blue);
  }
  .person__name {
    color: var(--accent-blue);
    font-size: 18px;
    line-height: 1.1;
  }
  .person__title {
    color: var(--accent-blue);
    font-size: 13px;
    margin-bottom: 10px;
  }
  .person__address {
    color: var(--ink);
    font-size: 13px;
    line-height: 1.35;
  }
  .details {
    list-style: none;
    padding-left: 14px;
    padding-top: 2px;
    color: var(--ink);
    font-size: 13.5px;
    line-height: 1.5;
  }
  .details li {
    display: flex;
    align-items: center;
    gap: 6px;
  }
  .details svg {
    width: 12px;
    height: 12px;
    flex: none;
  }
</style>
</head>
<body>
<main class="stage">

  <section class="card card--front" aria-label="Business card front">
    <div class="wordmark">
      <span class="wordmark__square"></span>
      <span class="wordmark__text">
        <span class="wordmark__main">Timber Crest</span>
        <span class="wordmark__sub">Construction</span>
      </span>
    </div>

    <div class="contact">
      <div class="person">
        <p class="person__name">Your Name</p>
        <p class="person__title">Title</p>
        <p class="person__address">Street Name City Name<br>State Zipcode</p>
      </div>
      <ul class="details">
        <li>
          <svg viewBox="0 0 12 12" aria-hidden="true"><circle cx="6" cy="6" r="5.3" fill="none" stroke="#1f1f1f" stroke-width="1"/><path d="M4 3.2 L5.2 3 L5.6 4.6 L4.9 5.1 Q5.6 6.6 6.9 7.2 L7.4 6.5 L9 6.9 L8.8 8.1 Q5 8.6 4 3.2Z" fill="#1f1f1f"/></svg>
          0412 555 019
        </li>
        <li>
          <svg viewBox="0 0 12 12" aria-hidden="true"><circle cx="6" cy="6" r="5.3" fill="none" stroke="#1f1f1f" stroke-width="1"/><path d="M4 3.2 L5.2 3 L5.6 4.6 L4.9 5.1 Q5.6 6.6 6.9 7.2 L7.4 6.5 L9 6.9 L8.8 8.1 Q5 8.6 4 3.2Z" fill="#1f1f1f"/></svg>
          0412 555 019
        </li>
        <li>
          <svg viewBox="0 0 12 12" aria-hidden="true"><circle cx="6" cy="6" r="6" fill="#1f1f1f"/><rect x="3" y="4" width="6" height="4.2" fill="#fff"/><path d="M3 4 L6 6.4 L9 4" fill="none" stroke="#1f1f1f" stroke-width="0.8"/></svg>
          hello@timbercrestbuild.com
        </li>
        <li>
          <svg viewBox="0 0 12 12" aria-hidden="true"><circle cx="6" cy="6" r="5.3" fill="#1f1f1f"/><ellipse cx="6" cy="6" rx="2.2" ry="5.3" fill="none" stroke="#fff" stroke-width="0.8"/><path d="M0.8 6 H11.2 M1.8 3.5 H10.2 M1.8 8.5 H10.2" stroke="#fff" stroke-width="0.8"/></svg>
          www.timbercrestbuild.com
        </li>
      </ul>
    </div>
  </section>

  <section class="card card--back" aria-label="Business card back">
    <div class="wordmark">
      <span class="wordmark__square"></span>
      <span class="wordmark__text">
        <span class="wordmark__main">Timber Crest</span>
        <span class="wordmark__sub">Construction</span>
      </span>
    </div>
  </section>

</main>
</body>
</html>
```